Allied Health team of Physiotherapists & Occupational Therapists seek a business card design

We have our new logo, we now need our new business cards and stationary. Tidewell: Oedema & Family Clinic is seeking a generic card design to represent our whole team and individual cards for each therapist that incorporates our new logo to communicate our holistic approach that is calming, nuturing, supportive and welcoming.
Our Physiotherapists and Occupational Therapists assess, treat and provide education for people who are at risk of or who have lymphoedema. This is often as a result of treatment for cancer. We provide pre-operative and post-operative management and cancer rehabilitation in our Pilates studio. Our team also consists of Physiotherapists who have a strong interest in pelvic floor and continence management for both men and women.

Target Market(s)

Mainly women health conscious

Industry/Entity Type

Allied Health: Physiotherapy / Occupational Therapy

Contact Information for Business Card

Address: 14 Gallivant Ave Frankston 3199 Phone: 84316570 fax: 8431 6578 Email: info@tidewellcareservices.com.au Website: tidewellcareservices.com.au Facebook address: facebook.com/TidewellOedemaAndFamilyCareClinic. Room to write appointments. Individual cards need to have name, office email and individual email and professional details

Requirements
Must have
• Logo as per uploaded documents

```html
<!DOCTYPE html>
<html lang="en">
<head>
<meta charset="utf-8">
<title>Tidewell: Oedema &amp; Family Clinic – Business Cards</title>
<link rel="stylesheet" href="https://fonts.googleapis.com/css2?family=Arimo:wght@400;700&family=Marcellus+SC&display=swap">
<style>
  :root {
    --stage: #2a2a2a;
    --card-black: #1c1c1c;
    --card-white: #ffffff;
    --peach: #f4a97a;
    --emboss: #3a3a3a;
    --text-light: #f2f2f2;
  }
  * { box-sizing: border-box; margin: 0; padding: 0; }
  html, body { width: 1200px; height: 1015px; overflow: hidden; }
  body {
    background: radial-gradient(ellipse at center, #3a3a3a 0%, var(--stage) 60%, #151515 100%);
    font-family: "Arimo", Arial, sans-serif;
    position: relative;
  }
  .card {
    position: absolute;
    left: 280px;
    width: 640px;
    height: 366px;
    background: var(--card-black);
    overflow: hidden;
    box-shadow: 0 14px 30px rgba(0,0,0,0.55);
  }
  .card--back { top: 110px; }
  .card--front { top: 540px; }

  /* Back card: tone-on-tone clinic name */
  .back-mark {
    position: absolute;
    inset: 0;
    display: flex;
    flex-direction: column;
    align-items: center;
    justify-content: center;
    gap: 14px;
  }
  .back-mark__circle {
    width: 26px; height: 26px;
    border: 2px solid var(--emboss);
    border-radius: 50%;
  }
  .back-mark__name {
    font-size: 20px;
    color: var(--emboss);
    letter-spacing: 0.04em;
  }

  /* Front card */
  .front-shape { position: absolute; inset: 0; }
  .front-mark {
    position: absolute;
    left: 380px; top: 108px;
    width: 250px;
    display: flex;
    flex-direction: column;
    align-items: center;
    gap: 10px;
  }
  .front-mark__circle {
    width: 22px; height: 22px;
    border: 2px solid var(--peach);
    border-radius: 50%;
  }
  .front-mark__name {
    font-size: 14px;
    color: var(--peach);
    text-align: center;
    line-height: 1.3;
  }
  .details {
    position: absolute;
    left: 38px; top: 40px;
    color: var(--text-light);
  }
  .details__name {
    font-family: "Marcellus SC", serif;
    font-size: 27px;
    letter-spacing: 0.12em;
    color: var(--peach);
    margin-bottom: 6px;
  }
  .details__credentials {
    font-size: 13px;
    line-height: 17px;
    margin-bottom: 12px;
  }
  .details__roles {
    font-size: 14px;
    font-weight: 700;
    line-height: 18px;
    margin-bottom: 14px;
  }
  .contact { list-style: none; font-size: 13px; }
  .contact__item {
    display: flex; align-items: center; gap: 9px;
    height: 20px;
  }
  .contact__icon { width: 14px; height: 14px; flex: none; }
</style>
</head>
<body>

<section class="card card--back" aria-label="Business card back">
  <div class="back-mark">
    <span class="back-mark__circle"></span>
    <span class="back-mark__name">Tidewell: Oedema &amp; Family Clinic</span>
  </div>
</section>

<section class="card card--front" aria-label="Business card front">
  <svg class="front-shape" width="640" height="366" viewBox="0 0 640 366" aria-hidden="true">
    <circle cx="532" cy="140" r="214" fill="none" stroke="var(--peach)" stroke-width="4"/>
    <circle cx="540" cy="132" r="212" fill="var(--card-white)"/>
    <rect x="540" y="0" width="100" height="345" fill="var(--card-white)"/>
  </svg>

  <div class="front-mark">
    <span class="front-mark__circle"></span>
    <span class="front-mark__name">Tidewell: Oedema &amp; Family Clinic</span>
  </div>

  <div class="details">
    <h1 class="details__name">Maren Holloway</h1>
    <p class="details__credentials">
      B. Physio (Hons), B.App.Sci.<br>
      (Human Movement/Psych)<br>
      Post Grad Certif. Exercise for Women<br>
      Post Grad Certif. Continence &amp;<br>
      Pelvic Floor Rehabilitation
    </p>
    <p class="details__roles">
      Physiotherapist<br>
      Lymphoedema &amp; Oncology Rehabilitation<br>
      Continence &amp; Pelvic Floor
    </p>
    <ul class="contact">
      <li class="contact__item">
        <svg class="contact__icon" viewBox="0 0 24 24"><path fill="var(--peach)" d="M6.6 10.8a15 15 0 0 0 6.6 6.6l2.2-2.2c.3-.3.7-.4 1-.2 1.1.4 2.3.6 3.6.6.6 0 1 .4 1 1V20c0 .6-.4 1-1 1A17 17 0 0 1 3 4c0-.6.4-1 1-1h3.5c.6 0 1 .4 1 1 0 1.3.2 2.5.6 3.6.1.3 0 .7-.2 1z"/></svg>
        <span>000 4444 5555</span>
      </li>
      <li class="contact__item">
        <svg class="contact__icon" viewBox="0 0 24 24"><path fill="var(--peach)" d="M2 5h20v14H2z"/><path fill="none" stroke="var(--card-black)" stroke-width="1.6" d="M2 5l10 8 10-8"/></svg>
        <span>info@tidewellcareservices.com.au</span>
      </li>
      <li class="contact__item">
        <svg class="contact__icon" viewBox="0 0 24 24"><path fill="var(--peach)" d="M2 5h20v14H2z"/><path fill="none" stroke="var(--card-black)" stroke-width="1.6" d="M2 5l10 8 10-8"/></svg>
        <span>name@tidewellcareservices.com.au</span>
      </li>
      <li class="contact__item">
        <svg class="contact__icon" viewBox="0 0 24 24"><g fill="none" stroke="var(--peach)" stroke-width="2"><circle cx="12" cy="12" r="10"/><ellipse cx="12" cy="12" rx="4.5" ry="10"/><path d="M2 12h20M4 7h16M4 17h16"/></g></svg>
        <span>www.tidewellcareservices.com.au</span>
      </li>
    </ul>
  </div>
</section>

</body>
</html>
```